RWT Fittings Ltd Business Cards

We need a business card with our business logo. We provide window and door installations on high-rises in west coast British Colombia, Canada.

I would like my business information and details on one side of the card, and the other side the company name with logo

Target Market(s)

General Contractors

Industry/Entity Type

Construction

Contact Information for Business Card

one side i want my company name and logo in the dark theme logo that i provided

Requirements
Must have
• Marco Peltieri, 16045518293, RWTFittings@mailbox-demo.com, 1407-5194 Linden Row Burnaby BC, V5H 2K9, Owner & Manager

```html
<!DOCTYPE html>
<html lang="en">
<head>
<meta charset="utf-8">
<title>RWT Fittings Ltd Business Cards</title>
<link rel="stylesheet" href="https://fonts.googleapis.com/css2?family=Roboto:wght@400;500;700&display=swap">
<style>
  :root {
    --page-bg: #232323;
    --card-dark: #1e1f23;
    --card-dark-2: #26282d;
    --accent-blue: #29a8e4;
    --name-gray: #a7a7a9;
    --text-white: #f2f2f2;
    --brand-muted: #3a3b40;
    --photo-dark: #1d1a17;
    --photo-mid: #4a443e;
    --photo-light: #6b645c;
  }
  * { box-sizing: border-box; margin: 0; padding: 0; }
  html, body {
    width: 1200px; height: 780px; overflow: hidden;
    background: var(--page-bg);
    font-family: "Roboto", Arial, sans-serif;
  }
  .sheet {
    position: relative; width: 1200px; height: 780px;
    display: flex; align-items: center; justify-content: center; gap: 50px;
  }
  .card {
    position: relative; width: 530px; height: 303px;
    border-radius: 4px; overflow: hidden;
    box-shadow: 0 18px 40px rgba(0,0,0,0.55);
  }

  /* Contact side */
  .card--contact { background: linear-gradient(160deg, var(--card-dark) 55%, var(--card-dark-2) 100%); }
  .card--contact .brand-mark {
    position: absolute; top: 26px; left: 28px;
    display: flex; align-items: center; gap: 10px;
    font-size: 20px; font-weight: 700; color: var(--brand-muted);
    letter-spacing: 0.5px;
  }
  .brand-mark .brand-square { width: 18px; height: 18px; background: var(--brand-muted); }
  .contact-block {
    position: absolute; right: 58px; bottom: 34px; text-align: right;
  }
  .person-name { font-size: 27px; font-weight: 700; line-height: 1.1; }
  .person-name .first { color: var(--accent-blue); }
  .person-name .last { color: var(--name-gray); }
  .person-role { font-size: 13px; font-weight: 500; color: var(--text-white); margin-top: 3px; }
  .person-address { font-size: 13px; color: var(--text-white); line-height: 1.35; margin-top: 14px; }
  .contact-line {
    display: flex; justify-content: flex-end; align-items: center; gap: 8px;
    font-size: 13px; color: var(--text-white); margin-top: 10px;
  }
  .contact-line + .contact-line { margin-top: 4px; }
  .contact-line svg { width: 14px; height: 14px; flex: none; }
  .accent-bar {
    position: absolute; right: 0; bottom: 150px;
    width: 26px; height: 34px; background: var(--accent-blue);
  }

  /* Brand side */
  .card--brand { display: flex; align-items: center; justify-content: center; }
  .brand-photo {
    position: absolute; inset: 0;
    background: radial-gradient(ellipse at 70% 40%, var(--photo-light) 0%, var(--photo-mid) 40%, var(--photo-dark) 100%);
  }
  .brand-lockup {
    position: relative; display: flex; align-items: center; gap: 14px;
    font-size: 42px; font-weight: 500; color: var(--accent-blue);
  }
  .brand-lockup .brand-square { width: 34px; height: 34px; background: var(--accent-blue); }
</style>
</head>
<body>
<main class="sheet">
  <section class="card card--contact" aria-label="Contact side">
    <div class="brand-mark"><span class="brand-square"></span>RWT Fittings Ltd</div>
    <div class="accent-bar"></div>
    <div class="contact-block">
      <p class="person-name"><span class="first">Marco</span> <span class="last">Peltieri</span></p>
      <p class="person-role">Owner &amp; Manager</p>
      <p class="person-address">1407-5194 Linden Row<br>Burnaby BC, V5H 2K9</p>
      <p class="contact-line">1604 551 8293
        <svg viewBox="0 0 24 24" aria-hidden="true"><path fill="var(--accent-blue)" d="M6.6 10.8a15 15 0 0 0 6.6 6.6l2.2-2.2a1 1 0 0 1 1-.25 11.4 11.4 0 0 0 3.6.57 1 1 0 0 1 1 1V20a1 1 0 0 1-1 1A17 17 0 0 1 3 4a1 1 0 0 1 1-1h3.5a1 1 0 0 1 1 1c0 1.25.2 2.45.57 3.57a1 1 0 0 1-.25 1z"/></svg>
      </p>
      <p class="contact-line">RWTFittings@mailbox-demo.com
        <svg viewBox="0 0 24 24" aria-hidden="true"><rect x="2" y="5" width="20" height="14" rx="2" fill="var(--accent-blue)"/><path d="M3 6l9 7 9-7" fill="none" stroke="var(--card-dark)" stroke-width="2"/></svg>
      </p>
    </div>
  </section>

  <section class="card card--brand" aria-label="Brand side">
    <div class="brand-photo" role="img" aria-label="Soft-focus photo of a dim modern interior with plants"></div>
    <div class="brand-lockup"><span class="brand-square"></span>RWT Fittings Ltd</div>
  </section>
</main>
</body>
</html>
```